Pell Dental Care Small Tote Bag

Pell Dental Care needs an advertisement design for a BrightKart Small Tote Bag. See website "www.pelldental-example.com." See uploaded files for small tote bag design template, color scheme, logos, and photo image of Dr. Pell. Designer may crop photo as necessary.

Target Market(s)

Target market is Adults ages 35 to 80.

Industry/Entity Type

Dental

Font styles to use
Sans Serif

```html
<!DOCTYPE html>
<html lang="en">
<head>
<meta charset="utf-8">
<title>Pell Dental Care – Small Tote Bag Print</title>
<link rel="stylesheet" href="https://fonts.googleapis.com/css2?family=Lato:wght@400;700;900&display=swap">
<style>
  :root {
    --fabric: #f4f2ec;
    --green-dark: #2c5647;
    --green-deep: #224438;
    --green-soft: #6f9d8e;
    --brown-soft: #7d6a5c;
    --white: #ffffff;
    --rule: #9aaaa4;
  }
  * { box-sizing: border-box; margin: 0; padding: 0; }
  html, body { width: 1200px; height: 1000px; overflow: hidden; }
  body {
    background: var(--fabric);
    font-family: "Lato", sans-serif;
    color: var(--green-dark);
  }
  .tote-print {
    position: absolute;
    left: 190px;
    top: 110px;
    width: 820px;
    height: 780px;
  }
  .brand {
    display: flex;
    align-items: center;
    justify-content: center;
    gap: 26px;
    height: 230px;
  }
  .brand-dot {
    width: 46px;
    height: 46px;
    border-radius: 50%;
    background: var(--green-soft);
  }
  .brand-name {
    font-size: 84px;
    font-weight: 700;
    color: var(--green-dark);
    letter-spacing: -0.5px;
  }
  .services {
    margin-top: 40px;
    background: var(--green-dark);
    height: 76px;
    display: grid;
    grid-template-columns: 1fr 1fr;
    align-content: center;
    row-gap: 4px;
    padding: 0 0 0 96px;
    color: var(--white);
    font-size: 25px;
    font-weight: 700;
    letter-spacing: 1.6px;
  }
  .services li { list-style: none; }
  .services li::before { content: "• "; }
  .contact {
    display: flex;
    align-items: center;
    height: 130px;
    padding-left: 26px;
  }
  .tagline {
    width: 270px;
    text-align: center;
    font-size: 26px;
    font-weight: 700;
    line-height: 1.38;
    color: var(--brown-soft);
  }
  .tagline .accent { color: var(--green-soft); }
  .phone-icon { width: 74px; height: 116px; margin: 0 18px 0 10px; }
  .call { color: var(--green-dark); font-weight: 900; }
  .call-lead { font-size: 40px; line-height: 1.1; }
  .call-number { font-size: 50px; line-height: 1.15; letter-spacing: 0.5px; }
  .rule {
    height: 2px;
    background: var(--rule);
    margin: 6px 30px 0;
  }
  .social {
    display: flex;
    justify-content: space-between;
    padding: 0 34px;
    height: 76px;
    align-items: center;
    font-size: 38px;
    font-weight: 700;
    color: var(--green-dark);
  }
  .social-item { display: flex; align-items: center; gap: 14px; }
  .social-dot {
    width: 38px; height: 38px; border-radius: 50%;
    background: var(--green-soft);
  }
  .web-bar {
    margin-top: 16px;
    height: 122px;
    background: linear-gradient(180deg, #3a6a5a 0%, var(--green-dark) 45%, var(--green-deep) 100%);
    display: flex;
    align-items: center;
    justify-content: center;
    color: var(--white);
    font-size: 56px;
    font-weight: 400;
  }
  .web-bar strong { font-weight: 900; }
</style>
</head>
<body>
  <main class="tote-print">
    <header class="brand">
      <span class="brand-dot"></span>
      <span class="brand-name">Pell Dental Care</span>
    </header>

    <ul class="services">
      <li>General Dentistry</li>
      <li>Beautiful Dentures</li>
      <li>Cosmetic Dentistry</li>
      <li>Sedation Dentistry</li>
    </ul>

    <section class="contact">
      <p class="tagline">
        Life-Changing<br>
        <span class="accent">Family Dental Care</span><br>
        In Cedar Vale
      </p>
      <svg class="phone-icon" viewBox="0 0 74 116" aria-hidden="true">
        <rect x="6" y="4" width="62" height="108" rx="10" fill="#2c5647"/>
        <rect x="14" y="14" width="46" height="36" rx="3" fill="#f4f2ec"/>
        <g fill="#f4f2ec">
          <rect x="14" y="58" width="12" height="9" rx="2"/><rect x="31" y="58" width="12" height="9" rx="2"/><rect x="48" y="58" width="12" height="9" rx="2"/>
          <rect x="14" y="72" width="12" height="9" rx="2"/><rect x="31" y="72" width="12" height="9" rx="2"/><rect x="48" y="72" width="12" height="9" rx="2"/>
          <rect x="14" y="86" width="12" height="9" rx="2"/><rect x="31" y="86" width="12" height="9" rx="2"/><rect x="48" y="86" width="12" height="9" rx="2"/>
        </g>
      </svg>
      <div class="call">
        <p class="call-lead">Call Us Today!</p>
        <p class="call-number">(555) 013-4820</p>
      </div>
    </section>

    <div class="rule"></div>

    <section class="social">
      <span class="social-item"><span class="social-dot"></span>Pell Dental Care</span>
      <span class="social-item"><span class="social-dot"></span>@PellDental</span>
    </section>

    <footer class="web-bar">
      <span>www.<strong>pelldental-example</strong>.com</span>
    </footer>
  </main>
</body>
</html>
```